Brivolt Technologies business card design

We need a business card designed with our new logo. it would be great if the card could communicate it is a technology based company.

Target Market(s)

system integrators

Industry/Entity Type

technology, IOT

Contact Information for Business Card

Name, designation, Address, telephone number, email address

Requirements
Must have
• logo and company name
Nice to have
• something to do with technology

```html
<!DOCTYPE html>
<html lang="en">
<head>
<meta charset="utf-8">
<title>Brivolt Technologies business card</title>
<link rel="stylesheet" href="https://fonts.googleapis.com/css2?family=Open+Sans:wght@400;600;700&display=swap">
<style>
  :root {
    --backdrop: #3a3a3a;
    --card: #1b1b1b;
    --card-back: #191919;
    --orange: #f7941d;
    --white: #f2f2f2;
    --grey: #d6d6d6;
    --mark: #262626;
  }
  * { margin: 0; padding: 0; box-sizing: border-box; }
  html, body {
    width: 1200px; height: 801px; overflow: hidden;
    background: var(--backdrop);
    font-family: "Open Sans", Arial, sans-serif;
  }
  .stage { position: relative; width: 1200px; height: 801px; }
  .card {
    position: absolute; width: 490px; height: 280px;
    border-bottom: 3px solid var(--orange);
    border-left: 2px solid var(--orange);
    box-shadow: 0 12px 30px rgba(0,0,0,.45);
  }
  .card--front { left: 70px; top: 260px; background: var(--card); }
  .card--back { left: 640px; top: 260px; background: var(--card-back); }

  .brand {
    position: absolute; left: 36px; top: 142px;
    display: flex; align-items: center; gap: 12px;
  }
  .brand__square { width: 28px; height: 28px; background: var(--orange); flex: none; }
  .brand__name {
    color: var(--white); font-weight: 700; font-size: 19px;
    letter-spacing: 1px; text-transform: uppercase; line-height: 1;
    white-space: nowrap;
  }

  .person {
    position: absolute; right: 34px; top: 30px; text-align: right;
  }
  .person__name {
    color: var(--orange); font-weight: 700; font-size: 17px;
    text-transform: uppercase; letter-spacing: .3px;
  }
  .person__title { color: var(--white); font-size: 12px; margin-top: 1px; }
  .person__rule {
    width: 250px; height: 1px; background: var(--orange);
    margin: 8px 0 10px auto;
  }
  .person__address { color: var(--grey); font-size: 12px; line-height: 1.5; }

  .contact {
    position: absolute; left: 36px; bottom: 20px; width: 280px;
  }
  .contact__rule { height: 1px; background: var(--orange); margin-bottom: 10px; }
  .contact__row {
    display: flex; align-items: center; gap: 8px;
    color: var(--grey); font-size: 12px; line-height: 19px;
  }
  .contact__row svg { width: 11px; height: 11px; flex: none; }

  .back-mark {
    position: absolute; left: 50%; top: 50%;
    width: 70px; height: 70px; margin: -35px 0 0 -35px;
    background: var(--mark);
  }
</style>
</head>
<body>
<div class="stage">
  <section class="card card--front">
    <div class="brand">
      <span class="brand__square"></span>
      <span class="brand__name">Brivolt Technologies</span>
    </div>

    <div class="person">
      <div class="person__name">Leo Hartwell</div>
      <div class="person__title">President</div>
      <div class="person__rule"></div>
      <div class="person__address">1870 Seacliff Harbor Dr<br>Seacliff CA 92600</div>
    </div>

    <div class="contact">
      <div class="contact__rule"></div>
      <div class="contact__row">
        <svg viewBox="0 0 12 12"><path fill="#f7941d" d="M2.5 1l2 2.2-1 1.3c.7 1.5 1.8 2.6 3.3 3.3l1.3-1 2.2 2-1.3 1.9C4.6 10.4 1.6 7.4 .8 2.4z"/></svg>
        949-555-0172
      </div>
      <div class="contact__row">
        <svg viewBox="0 0 12 12"><rect x="1" y="2.5" width="10" height="7" fill="#f7941d"/><path d="M1 2.5l5 4 5-4" stroke="#1b1b1b" fill="none"/></svg>
        info@brivolttech.com
      </div>
      <div class="contact__row">
        <svg viewBox="0 0 12 12"><circle cx="6" cy="6" r="5" fill="none" stroke="#f7941d" stroke-width="1.4"/><path d="M1 6h10M6 1c-2.5 3-2.5 7 0 10M6 1c2.5 3 2.5 7 0 10" stroke="#f7941d" fill="none"/></svg>
        www.brivolttech.com
      </div>
    </div>
  </section>

  <section class="card card--back">
    <div class="back-mark"></div>
  </section>
</div>
</body>
</html>
```